Local fast-growing company in the service sector

We are looking for a modern business card design, which should also appear on our letterheads

Target Market(s)

Private and industrial sectors

Contact Information for Business Card

Vorname Name
Kellberger Str. 18
73614 Sandbrunn
Tel.: 07146-839214-0
Name@agentur-kvtl.de

Colors
9d9d9d
919191
aaaaaa

Requirements
Must have
• The logo (file) in silver

```html
<!DOCTYPE html>
<html lang="de">
<head>
<meta charset="utf-8">
<title>KVTL Visitenkarte</title>
<link rel="stylesheet" href="https://fonts.googleapis.com/css2?family=Lexend:wght@400;600&family=Orbitron:wght@700&display=swap">
<style>
  :root {
    --page: #e4e4e4;
    --card-dark: #2b2b2c;
    --card-dark-glow: #3d3d3e;
    --card-light: #f3f3f3;
    --ink: #222223;
    --silver: #aaaaaa;
  }
  * { margin: 0; padding: 0; box-sizing: border-box; }
  html, body { width: 1200px; height: 576px; overflow: hidden; background: var(--page); }
  .canvas { position: relative; width: 1200px; height: 576px; }
  .card {
    position: absolute; top: 138px; width: 484px; height: 294px;
    border-radius: 12px; overflow: hidden;
  }
  .card-front {
    left: 82px;
    background: radial-gradient(ellipse at 50% 35%, var(--card-dark-glow), var(--card-dark) 70%);
  }
  .card-back { left: 600px; background: var(--card-light); }
  .card-back .curve { position: absolute; inset: 0; width: 100%; height: 100%; }
  .brand-name {
    position: absolute; font-family: "Lexend", sans-serif; font-weight: 600;
    color: var(--silver); letter-spacing: 2px; line-height: 1;
  }
  .card-front .brand-name { left: 0; right: 0; top: 126px; text-align: center; font-size: 64px; }
  .card-back .brand-name { left: 322px; top: 128px; font-size: 36px; }
  .person-name {
    position: absolute; left: 25px; top: 36px;
    font-family: "Orbitron", sans-serif; font-weight: 700; font-size: 16.5px;
    letter-spacing: 1.6px; color: var(--ink);
  }
  .contact {
    position: absolute; left: 25px; top: 202px; list-style: none;
    font-family: "Lexend", sans-serif; font-size: 13px; line-height: 17px; color: var(--ink);
  }
  .contact li { display: flex; align-items: center; gap: 9px; }
  .contact svg { width: 10px; height: 10px; fill: var(--ink); }
</style>
</head>
<body>
<main class="canvas">
  <section class="card card-front" aria-label="Vorderseite">
    <span class="brand-name">KVTL</span>
  </section>

  <section class="card card-back" aria-label="Rückseite">
    <svg class="curve" viewBox="0 0 484 294" preserveAspectRatio="none" aria-hidden="true">
      <defs>
        <radialGradient id="darkFill" cx="70%" cy="45%" r="60%">
          <stop offset="0" stop-color="#3d3d3e"/>
          <stop offset="1" stop-color="#2b2b2c"/>
        </radialGradient>
      </defs>
      <path d="M256 0 C 205 80, 200 200, 246 294 L 252 294 C 208 200, 214 85, 263 0 Z" fill="#2b2b2c"/>
      <path d="M272 0 C 214 90, 214 210, 264 294 L 484 294 L 484 0 Z" fill="url(#darkFill)"/>
    </svg>
    <h1 class="person-name">VORNAME NAME</h1>
    <ul class="contact">
      <li>Kellberger Str. 18</li>
      <li>73614 Sandbrunn</li>
      <li>
        <svg viewBox="0 0 10 10" aria-label="Telefon"><path d="M1 3 Q5 0 9 3 L8 4.5 L6.5 3.8 L6.5 3 Q5 2.5 3.5 3 L3.5 3.8 L2 4.5 Z M2.5 5 H7.5 L8.5 9 H1.5 Z"/></svg>
        07146-839214-0
      </li>
      <li>
        <svg viewBox="0 0 10 10" aria-label="E-Mail"><path d="M0.5 2 H9.5 V8 H0.5 Z M1 2.5 L5 5.5 L9 2.5"/></svg>
        Name@agentur-kvtl.de
      </li>
    </ul>
    <span class="brand-name">KVTL</span>
  </section>
</main>
</body>
</html>
```